Web Site Design for a Finance (lending) Company

We are opening a new subsidiary that focuses on lending money in the real estate industry. We need a web site designed to represent the business.

The business is lending money to real estate investors. A typical client/borrower will be looking to borrow money to buy a house, renovate it and then sell it at a profit, all within 12 months or less.

Company name is RTV Finance. Our logo is attached.

Attached is a general outline for the web site. We're working on writing more text for each page but this should give you enough to get started with some ideas.

Competitor web site that I like a lot (as an example): https://dorvaleqcapital.example/. Many of the general items on this site match what we will need (description of loan programs, FAQ)

Target Market(s)

Real estate investors (generally individuals or small companies with just a few people) who are buying homes, renovating them and then selling them at a profit.

Industry/Entity Type

Finance

Coding

Coded - Design and coding required

Number of Pages Required

5+ page

Colors

Designer to choose colors to be used in the design.

Requirements
Must have
• Minimalist design. Clean lines without too much clutter. Some stock photography is ok but the photos should not be distracting. They should almost fade in to the background so that user can focus on the key information about what our company does instead. We are a finance company, not a design company, so the information about our products will be more interesting to site visitors than the art.
• Some minimalist examples from Snapboard:
• https://www.snapboardia.example/explore/minimalist-web-design/
Nice to have
• If you search in zoovle for "hard money lenders" you will find many examples of web sites from our competition. I have provided a link above to competitor web site that I like a lot.
• I have attached our logo in EPS format. Logo is green. Web site doesn't have to be green but it should be of a color that will work well with the logo.

```html
<!DOCTYPE html>
<html lang="en">
<head>
<meta charset="utf-8">
<title>RTV Finance</title>
<link href="https://fonts.googleapis.com/css2?family=Roboto:wght@300;400;500;700&family=Open+Sans:wght@400;600;700&display=swap" rel="stylesheet">
<style>
:root{
  --green:#0b5a33;
  --green-dark:#084526;
  --grey:#8f9a94;
  --grey-light:#b9c4be;
  --text:#555;
  --white:#fff;
  --bar:#8b8f8c;
}
*{box-sizing:border-box;margin:0;padding:0}
html,body{width:1200px;height:3838px;overflow:hidden}
body{font-family:"Open Sans",Arial,sans-serif;color:var(--text);background:var(--white);position:relative}
h1,h2,h3,h4{font-family:"Roboto",Arial,sans-serif;font-weight:400}
.abs{position:absolute}
p{font-size:14px;line-height:26px}

/* header */
.site-header{position:absolute;top:0;left:0;width:1200px;height:115px;z-index:5}
.brand{position:absolute;left:77px;top:30px;display:flex;align-items:center;gap:12px}
.brand-square{width:26px;height:26px;background:var(--green)}
.brand-name{font-family:"Roboto",sans-serif;font-weight:700;font-size:28px;color:var(--green)}
.phone{position:absolute;right:77px;top:12px;display:flex;align-items:center;gap:10px;font-family:"Roboto",sans-serif;font-weight:500;font-size:26px;color:var(--green-dark)}
.phone-icon{width:40px;height:40px;border-radius:50%;background:var(--green);display:flex;align-items:center;justify-content:center}
.main-nav{position:absolute;right:77px;top:60px;display:flex;align-items:center;gap:0}
.main-nav a{font-family:"Roboto",sans-serif;font-size:16px;color:#333;text-decoration:none;padding:10px 17px}
.main-nav a.active{background:var(--green);color:var(--white)}

/* hero */
.hero{position:absolute;top:0;left:0;width:1200px;height:660px}
.hero-photo{position:absolute;inset:0;background:linear-gradient(100deg,#e9ece9 0%,#d4d8d3 35%,#b9b3a8 60%,#dfe1dc 100%)}
.hero-title{position:absolute;left:77px;top:268px;font-family:"Roboto",sans-serif;font-weight:700;font-size:42px;line-height:53px;color:var(--white);text-shadow:0 2px 6px rgba(0,0,0,.25)}
.btn{display:inline-block;font-family:"Roboto",sans-serif;font-weight:500;font-size:18px;text-decoration:none}
.btn-solid{background:var(--green);color:var(--white);padding:17px 36px}
.btn-outline{border:2px solid var(--white);color:var(--white);padding:17px 28px}
.hero .btn-solid{position:absolute;left:77px;top:446px}
.slider-dots{position:absolute;left:1156px;top:260px;display:flex;flex-direction:column;gap:20px}
.slider-dots span{width:15px;height:15px;border-radius:50%;background:var(--white)}
.slider-dots span.on{background:var(--green)}

/* welcome */
.welcome{position:absolute;top:590px;left:0;width:1200px;height:433px;background:var(--green);clip-path:polygon(0 45px,50% 0,100% 45px,100% 100%,0 100%);text-align:center;color:var(--white)}
.welcome h2{margin-top:110px;font-size:40px}
.welcome h2 .accent{color:var(--grey-light)}
.welcome p{width:960px;margin:20px auto 0;font-size:13.5px;color:#e4ece7}
.welcome .btn-outline{margin-top:30px;padding:16px 28px}
.accent{color:var(--grey)}

/* about */
.about{position:absolute;top:1023px;left:0;width:1200px;height:469px;text-align:center}
.section-title{font-size:42px;color:var(--green)}
.about .section-title{margin-top:58px}
.feature{position:absolute;top:130px;width:300px;text-align:center}
.feature-icon{width:124px;height:124px;border-radius:50%;margin:0 auto;display:flex;align-items:center;justify-content:center;box-shadow:0 6px 10px rgba(0,0,0,.25)}
.feature-icon.green{background:var(--green)}
.feature-icon.grey{background:#8d8f8e}
.feature h3{margin-top:38px;font-size:17px;color:var(--green);font-weight:500}
.feature p{margin-top:14px;font-size:13.5px;line-height:26px;padding:0 20px}
.feature .arrow{margin-top:16px}

/* split loans */
.loan{position:absolute;left:0;width:1200px;height:470px;overflow:hidden}
.loan-photo{position:absolute;inset:0}
.loan-panel{position:absolute;inset:0;background:var(--green)}
.loan h2{position:absolute;font-size:40px;color:var(--white);line-height:52px}
.loan h2 .accent{color:var(--grey-light)}
.loan p{position:absolute;font-size:13.5px;color:#e4ece7}
.loan .why{position:absolute;font-size:16px;font-style:italic;color:var(--white);text-decoration:underline}
.loan .btn-outline{position:absolute;padding:16px 26px}

/* testimonials */
.clients{position:absolute;top:1962px;left:0;width:1200px;height:371px;text-align:center}
.clients .section-title{margin-top:50px}
.client-card{position:absolute;top:130px;width:504px;height:180px;background:var(--white);box-shadow:0 0 14px rgba(0,0,0,.14);text-align:left}
.client-avatar{position:absolute;left:22px;top:22px;width:104px;height:104px;background:linear-gradient(160deg,#d9d2c9,#a99a8d)}
.client-name{position:absolute;left:128px;top:22px;font-family:"Roboto",sans-serif;font-size:17px;color:var(--green)}
.client-site{position:absolute;left:128px;top:48px;font-size:12px;color:#777}
.client-card p{position:absolute;left:128px;top:78px;width:340px;font-size:13px;line-height:25px}
.quote-icon{position:absolute;right:24px;top:30px}

/* blog */
.blog{position:absolute;top:2801px;left:0;width:1200px;height:537px;text-align:center}
.blog .section-title{margin-top:52px}
.post{position:absolute;top:128px;width:324px;text-align:left}
.post-photo{width:324px;height:210px}
.post-date{position:absolute;left:0;top:168px;width:92px;height:90px;background:var(--green);color:var(--white);text-align:center;font-family:"Roboto",sans-serif}
.post-date b{display:block;font-size:38px;font-weight:700;margin-top:10px}
.post-date span{font-size:15px}
.post h4{position:absolute;left:104px;top:222px;font-size:15px;font-weight:700;line-height:22px;color:#222}
.post p{position:absolute;left:0;top:276px;font-size:13px;line-height:25px}
.live-chat{position:absolute;left:1152px;top:2988px;width:48px;height:192px;background:#8b8f8c;border-radius:6px 0 0 6px}
.live-chat .label{position:absolute;left:0;top:0;width:48px;height:140px;display:flex;align-items:center;justify-content:center}
.live-chat .label span{transform:rotate(-90deg);white-space:nowrap;color:var(--white);font-family:"Roboto",sans-serif;font-size:16px;letter-spacing:1px}
.live-chat .chat-btn{position:absolute;left:0;bottom:0;width:48px;height:48px;background:var(--green);display:flex;align-items:center;justify-content:center}

/* footer */
.site-footer{position:absolute;top:3338px;left:0;width:1200px;height:435px;background:var(--green);clip-path:polygon(0 50px,50% 0,100% 50px,100% 100%,0 100%);color:var(--white)}
.footer-col{position:absolute;top:115px}
.footer-col h4{font-size:16px;font-weight:700;margin-bottom:18px}
.footer-col p{font-size:13px;line-height:27px;color:#e4ece7}
.read-more{display:inline-block;margin-top:8px;font-weight:700;font-size:14px;color:var(--white);text-decoration:underline}
.social{display:flex;gap:12px;margin-top:20px}
.social span{width:40px;height:40px;border-radius:50%;border:2px solid rgba(255,255,255,.6);background:rgba(255,255,255,.12)}
.contact-line{display:flex;gap:16px;align-items:flex-start;margin-bottom:16px;font-size:13px;line-height:26px}
.contact-line strong{font-size:14px}
.footer-form .field{width:333px;height:41px;background:var(--white);margin-bottom:6px;padding:10px 12px;font-size:13px;color:#777}
.footer-form .submit{display:inline-block;margin-top:6px;border:2px solid var(--white);padding:8px 28px;font-family:"Roboto",sans-serif;font-size:17px}
.copyright{position:absolute;top:3773px;left:0;width:1200px;height:65px;background:var(--bar);color:var(--white);text-align:center;line-height:65px;font-size:13px}
.copyright b{color:#0e6a3a}
</style>
</head>
<body>

<section class="hero">
  <div class="hero-photo" role="img" aria-label="Photo of a couple viewing a bright empty house interior with an agent"></div>
  <h1 class="hero-title">LOCAL REAL ESTATE EXPERTS<br>LENDING TO LOCAL REAL<br>ESTATE INVESTORS</h1>
  <a class="btn btn-solid" href="#">CONTACT US</a>
  <div class="slider-dots"><span></span><span></span><span class="on"></span><span></span><span></span></div>
</section>

<header class="site-header">
  <div class="brand"><span class="brand-square"></span><span class="brand-name">RTV Finance</span></div>
  <div class="phone">
    <span class="phone-icon"><svg width="20" height="20" viewBox="0 0 24 24"><path fill="#fff" d="M6.6 10.8a15.1 15.1 0 0 0 6.6 6.6l2.2-2.2c.3-.3.7-.4 1-.2 1.1.4 2.3.6 3.6.6.6 0 1 .4 1 1V20c0 .6-.4 1-1 1C10.6 21 3 13.4 3 4c0-.6.4-1 1-1h3.5c.6 0 1 .4 1 1 0 1.3.2 2.5.6 3.6.1.3 0 .7-.2 1z"/></svg></span>
    123-456-7890
  </div>
  <nav class="main-nav">
    <a class="active" href="#">HOME</a><a href="#">ABOUT US</a><a href="#">LOANS</a><a href="#">RESOURCES</a><a href="#">CONTACT US</a>
    <svg width="22" height="22" viewBox="0 0 24 24" style="margin-left:8px"><circle cx="10" cy="10" r="6.5" fill="none" stroke="#333" stroke-width="2.5"/><line x1="15" y1="15" x2="21" y2="21" stroke="#333" stroke-width="3"/></svg>
  </nav>
</header>

<section class="welcome">
  <h2>WELCOME TO <span class="accent">RTV FINANCE</span></h2>
  <p>Lorem Ipsum is simply dummy text of the printing and typesetting industry. Lorem Ipsum has been the industry's standard dummy text ever since the 1500s, when an unknown printer took a galley of type and scrambled.</p>
  <p style="margin-top:12px">Lorem Ipsum is simply dummy text of the printing and typesetting industry. Lorem Ipsum has been the industry's standard dummy text ever since the 1500s, when an unknown printer took a galley of type and scrambled it to make a type specimen book. It has survived not only five centuries, but also the leap into electronic typesetting, remaining essentially unchanged.</p>
  <a class="btn btn-outline" href="#">KNOW MORE</a>
</section>

<section class="about">
  <h2 class="section-title">ABOUT US</h2>
  <div class="feature" style="left:101px">
    <div class="feature-icon green"><svg width="64" height="64" viewBox="0 0 64 64"><circle cx="30" cy="34" r="22" fill="none" stroke="#fff" stroke-width="5"/><circle cx="30" cy="34" r="12" fill="none" stroke="#fff" stroke-width="5"/><circle cx="30" cy="34" r="4" fill="#fff"/><line x1="30" y1="34" x2="54" y2="10" stroke="#fff" stroke-width="4"/><path d="M50 6l8 0-2 8-8 0z" fill="#fff"/></svg></div>
    <h3>MISSION</h3>
    <p>Lorem Ipsum is simply dummy text of the printing and typesetting industry.</p>
    <svg class="arrow" width="36" height="16" viewBox="0 0 36 16"><line x1="0" y1="8" x2="28" y2="8" stroke="#0b5a33" stroke-width="3"/><path d="M24 1l10 7-10 7z" fill="#0b5a33"/></svg>
  </div>
  <div class="feature" style="left:451px">
    <div class="feature-icon grey"><svg width="66" height="66" viewBox="0 0 66 66"><circle cx="33" cy="33" r="22" fill="none" stroke="#fff" stroke-width="4"/><circle cx="33" cy="33" r="9" fill="none" stroke="#fff" stroke-width="4"/><line x1="33" y1="3" x2="33" y2="20" stroke="#fff" stroke-width="4"/><line x1="33" y1="46" x2="33" y2="63" stroke="#fff" stroke-width="4"/><line x1="3" y1="33" x2="20" y2="33" stroke="#fff" stroke-width="4"/><line x1="46" y1="33" x2="63" y2="33" stroke="#fff" stroke-width="4"/></svg></div>
    <h3>FOCUS</h3>
    <p>Lorem Ipsum is simply dummy text of the printing and typesetting industry.</p>
    <svg class="arrow" width="36" height="16" viewBox="0 0 36 16"><line x1="0" y1="8" x2="28" y2="8" stroke="#0b5a33" stroke-width="3"/><path d="M24 1l10 7-10 7z" fill="#0b5a33"/></svg>
  </div>
  <div class="feature" style="left:802px">
    <div class="feature-icon grey"><svg width="66" height="66" viewBox="0 0 66 66"><text x="6" y="24" fill="#fff" font-family="Roboto,sans-serif" font-size="24" font-weight="700">$</text><rect x="8" y="46" width="8" height="14" fill="#fff"/><rect x="22" y="38" width="8" height="22" fill="#fff"/><rect x="36" y="30" width="8" height="30" fill="#fff"/><rect x="50" y="20" width="8" height="40" fill="#fff"/><path d="M24 26l14-12" stroke="#fff" stroke-width="3"/><path d="M34 10l8 0-2 8z" fill="#fff"/></svg></div>
    <h3>WHAT MAKES RTV DIFFERENT</h3>
    <p>Lorem Ipsum is simply dummy text of the printing and typesetting industry.</p>
    <svg class="arrow" width="36" height="16" viewBox="0 0 36 16"><line x1="0" y1="8" x2="28" y2="8" stroke="#0b5a33" stroke-width="3"/><path d="M24 1l10 7-10 7z" fill="#0b5a33"/></svg>
  </div>
</section>

<section class="loan" style="top:1492px">
  <div class="loan-photo" role="img" aria-label="Photo of a large two-storey suburban house under a blue sky" style="background:linear-gradient(180deg,#8fb3d6 0%,#c9d7e2 35%,#b9ab95 60%,#7f8c6c 100%)"></div>
  <div class="loan-panel" style="clip-path:polygon(0 0,640px 0,525px 100%,0 100%)"></div>
  <h2 style="left:77px;top:50px">FIX AND FLIP <span class="accent">LOANS</span></h2>
  <p style="left:77px;top:120px;width:400px">Lorem Ipsum is simply dummy text of the printing and typesetting industry. Lorem Ipsum is simply .</p>
  <p style="left:77px;top:190px;width:400px">Lorem Ipsum is simply dummy text of the printing and typesetting industry. Lorem Ipsum is simply dummy text of the printing and typesetting industry. Lorem Ipsum is simply dummy text of the printing.</p>
  <a class="why" style="left:77px;top:306px" href="#">Why Choose RTV ?</a>
  <a class="btn btn-outline" style="left:77px;top:350px" href="#">KNOW MORE</a>
</section>

<section class="clients">
  <h2 class="section-title">WHAT OUR <span class="accent">CLIENT SAY</span></h2>
  <div class="client-card" style="left:77px">
    <div class="client-avatar" role="img" aria-label="Client portrait"></div>
    <div class="client-name">CLIENT NAME</div>
    <div class="client-site">something.com</div>
    <p>Lorem Ipsum is simply dummy text of the printing and typesetting industry. Lorem Ipsum has been the industry's standard dummy text ever.</p>
    <svg class="quote-icon" width="30" height="28" viewBox="0 0 30 28"><path d="M2 2h26v18H10l-6 6v-6H2z" fill="none" stroke="#0b5a33" stroke-width="2.5"/><line x1="8" y1="9" x2="22" y2="9" stroke="#0b5a33" stroke-width="2"/><line x1="8" y1="14" x2="18" y2="14" stroke="#0b5a33" stroke-width="2"/></svg>
  </div>
  <div class="client-card" style="left:622px">
    <div class="client-avatar" role="img" aria-label="Client portrait"></div>
    <div class="client-name">CLIENT NAME</div>
    <div class="client-site">something.com</div>
    <p>Lorem Ipsum is simply dummy text of the printing and typesetting industry. Lorem Ipsum has been the industry's standard dummy text ever.</p>
    <svg class="quote-icon" width="30" height="28" viewBox="0 0 30 28"><path d="M2 2h26v18H10l-6 6v-6H2z" fill="none" stroke="#0b5a33" stroke-width="2.5"/><line x1="8" y1="9" x2="22" y2="9" stroke="#0b5a33" stroke-width="2"/><line x1="8" y1="14" x2="18" y2="14" stroke="#0b5a33" stroke-width="2"/></svg>
  </div>
</section>

<section class="loan" style="top:2333px;height:468px">
  <div class="loan-photo" role="img" aria-label="Photo of a hand holding house keys in front of a glass office tower" style="background:linear-gradient(160deg,#dfe6ee 0%,#9fb3c6 40%,#d7b79a 70%,#cfd6de 100%)"></div>
  <div class="loan-panel" style="clip-path:polygon(563px 0,1200px 0,1200px 100%,742px 100%)"></div>
  <h2 style="right:77px;top:48px;text-align:right">COMMERCIAL HARD<br><span class="accent">MONEY LOANS</span></h2>
  <p style="right:77px;top:170px;width:430px;text-align:right">Lorem Ipsum is simply dummy text of the printing and typesetting industry. Lorem Ipsum is simply dummy text of the printing and typesetting industry. Lorem Ipsum is simply dummy text of the printing.</p>
  <a class="why" style="right:77px;top:302px" href="#">Why Choose RTV ?</a>
  <a class="btn btn-outline" style="right:77px;top:344px" href="#">KNOW MORE</a>
</section>

<section class="blog">
  <h2 class="section-title">LATEST <span class="accent">BLOG</span></h2>
  <article class="post" style="left:77px">
    <div class="post-photo" role="img" aria-label="Photo of a small house model beside paperwork and a pen" style="background:linear-gradient(135deg,#e6e6e4,#a9aaa6)"></div>
    <div class="post-date"><b>03</b><span>Oct</span></div>
    <h4>LOREM IPSUM IS THE SIMPL<br>DUMMY PRINT TEXT</h4>
    <p>Lorem Ipsum is simply dummy text of the print printing and typesetting industry. Lorem Ipsum has been the industry's standard</p>
  </article>
  <article class="post" style="left:440px">
    <div class="post-photo" role="img" aria-label="Photo of two people reviewing documents at a desk" style="background:linear-gradient(135deg,#c9d3dc,#6f7f8c)"></div>
    <div class="post-date"><b>03</b><span>Oct</span></div>
    <h4>LOREM IPSUM IS THE SIMPL<br>DUMMY PRINT TEXT</h4>
    <p>Lorem Ipsum is simply dummy text of the print printing and typesetting industry. Lorem Ipsum has been the industry's standard</p>
  </article>
  <article class="post" style="left:801px">
    <div class="post-photo" role="img" aria-label="Photo of hands exchanging cash and a house sketch" style="background:linear-gradient(135deg,#eeeeec,#b3ada2)"></div>
    <div class="post-date"><b>03</b><span>Oct</span></div>
    <h4>LOREM IPSUM IS THE SIMPL<br>DUMMY PRINT TEXT</h4>
    <p>Lorem Ipsum is simply dummy text of the print printing and typesetting industry. Lorem Ipsum has been the industry's standard</p>
  </article>
</section>

<aside class="live-chat">
  <div class="label"><span>LIVE CHAT</span></div>
  <div class="chat-btn"><svg width="22" height="22" viewBox="0 0 24 24"><path fill="#fff" d="M6.6 10.8a15.1 15.1 0 0 0 6.6 6.6l2.2-2.2c.3-.3.7-.4 1-.2 1.1.4 2.3.6 3.6.6.6 0 1 .4 1 1V20c0 .6-.4 1-1 1C10.6 21 3 13.4 3 4c0-.6.4-1 1-1h3.5c.6 0 1 .4 1 1 0 1.3.2 2.5.6 3.6.1.3 0 .7-.2 1z"/></svg></div>
</aside>

<footer class="site-footer">
  <div class="footer-col" style="left:77px;width:300px">
    <h4>ABOUT US</h4>
    <p>Lorem Ipsum is simply dummy text of the printing and typesetting industry. Lorem Ipsum has been the industry's Ipsum is simply dummy text of the printing and typesetting industrsum has been the industry's standard dummy.</p>
    <a class="read-more" href="#">Read More...</a>
    <div class="social" aria-label="Social links"><span></span><span></span><span></span></div>
  </div>
  <div class="footer-col" style="left:440px;width:300px">
    <h4>GET IN TOUCH</h4>
    <div class="contact-line">
      <svg width="18" height="24" viewBox="0 0 18 24"><path d="M9 0a9 9 0 0 0-9 9c0 7 9 15 9 15s9-8 9-15a9 9 0 0 0-9-9z" fill="#fff"/><circle cx="9" cy="9" r="3.5" fill="#0b5a33"/></svg>
      <div><strong>RTV FINANCE</strong><br>101 - Lorem Ipsum is simple&nbsp; text<br>of print and type setting os the<br>industries print text.</div>
    </div>
    <div class="contact-line"><svg width="18" height="18" viewBox="0 0 24 24"><path fill="#fff" d="M6.6 10.8a15.1 15.1 0 0 0 6.6 6.6l2.2-2.2c.3-.3.7-.4 1-.2 1.1.4 2.3.6 3.6.6.6 0 1 .4 1 1V20c0 .6-.4 1-1 1C10.6 21 3 13.4 3 4c0-.6.4-1 1-1h3.5c.6 0 1 .4 1 1 0 1.3.2 2.5.6 3.6.1.3 0 .7-.2 1z"/></svg><span>123 456 7890</span></div>
    <div class="contact-line"><svg width="18" height="14" viewBox="0 0 18 14"><rect width="18" height="14" fill="#fff"/><path d="M0 0l9 7 9-7" fill="none" stroke="#0b5a33" stroke-width="1.5"/></svg><span>info@RTVfinance.com</span></div>
  </div>
  <div class="footer-col footer-form" style="left:788px;width:340px">
    <h4>CONTACT US</h4>
    <div class="field">Name*</div>
    <div class="field">E-mail*</div>
    <div class="field">Phone *</div>
    <div class="field">How you heard about us *</div>
    <div class="submit">SUBMIT</div>
  </div>
</footer>

<div class="copyright">© <b>RTV FINANCE</b> - 2017 All Right Reserved</div>

</body>
</html>
```